Business card for Crestline Bathrooms

Please design a business card for our bathroom renovation business. You can use my existing logo, but if you have an idea to modernize it, I would like to see it. Please see attached files first. I would like to use the blue and the orange theme. I like the concept of using the shower head in the logo. Please find following a design (or two) that I have been trying to create with my limited resources. That design was for a sign, but I was going to adopt it and use it as a business card as well. I like the concept of the water splash but I don’t think it “flows” nicely together with the logo. Another thought is that maybe creating the logo out of water splash could work and have a dramatic effect (like the water text and the butterfly picture attached with similar background instead of white). If the above doesn’t work I would like to see a modern simplified design. One of the attached files named as the unwanted business card has all the details that I want included in the business card. Please note that it is two sided.
Updates

I am very thankful for the designs that I have received, but they are very similar and only a couple of attempts to do something with the water splash as per my original brief. Modernizing the logo and having it made out of out of water splash with the orange as color accent could work and have a dramatic effect (like the water text and the butterfly picture attached with similar background instead of white). Please do not use the butterfly itself! This is just an example that images can be created out of water splash.

Contact Information for Business Card

all the details are on the unwonted business card file included

Colors
3176b5

Requirements
Nice to have
• Copied from the brief:
• ... maybe creating the logo out of water splash could work and have a dramatic effect (like the water text and the butterfly picture attached with similar background instead of white). Please do not use the butterfly itself!
Should not have
• I am getting designs with a butterfly. The butterfly picture was an example of creating something from a water splash. The butterfly itself has no association with anything other than the concept of creating a logo out of water splash. Sorry, I thought I was clear in the brief.

```html
<!DOCTYPE html>
<html lang="en">
<head>
<meta charset="utf-8">
<title>Crestline Bathrooms – Business Card</title>
<link href="https://fonts.googleapis.com/css2?family=Roboto:wght@400&family=Roboto+Condensed:wght@400&family=Short+Stack&display=swap" rel="stylesheet">
<style>
  :root {
    --navy: #06406b;
    --coral: #ec786b;
    --white: #ffffff;
    --ink: #4a4a4a;
    --badge: #6b6b6b;
    --backdrop: #e6e6e6;
    --water-light: #e4f4fb;
    --water-mid: #8fd0ef;
    --water-deep: #2a8fd6;
  }
  * { box-sizing: border-box; margin: 0; padding: 0; }
  html, body { width: 1200px; height: 960px; overflow: hidden; }
  body { background: var(--backdrop); position: relative; font-family: "Roboto", Arial, sans-serif; }

  .card { position: absolute; width: 600px; height: 344px; overflow: hidden; }

  /* Front side */
  .card-front { left: 314px; top: 113px; background: var(--navy); }
  .front-sweep { position: absolute; left: 0; top: 0; width: 600px; height: 344px; }
  .front-brand {
    position: absolute; left: 236px; top: 58px;
    display: flex; align-items: center; gap: 16px;
  }
  .front-brand-dot { width: 30px; height: 30px; border-radius: 50%; background: var(--coral); flex: none; }
  .front-brand-name {
    font-family: "Short Stack", "Comic Sans MS", cursive;
    font-size: 34px; line-height: 1.15; color: var(--white);
  }
  .holder-name {
    position: absolute; right: 31px; top: 176px;
    font-family: "Short Stack", "Comic Sans MS", cursive; font-weight: 400;
    font-size: 23px; letter-spacing: 0.5px; color: var(--coral);
  }
  .contact-list { position: absolute; right: 32px; top: 218px; list-style: none; text-align: right; }
  .contact-list li {
    display: flex; justify-content: flex-end; align-items: center;
    height: 19.5px; font-size: 14px; color: var(--white);
  }
  .contact-list li svg { width: 13px; height: 13px; margin-left: 8px; fill: var(--coral); }
  .contact-list li.postal { margin-top: 5px; font-size: 14.5px; }

  /* Back side */
  .card-back { left: 311px; top: 472px; background: var(--white); }
  .water-glow {
    position: absolute; left: 0; right: 0; bottom: 0; height: 190px;
    background: linear-gradient(to bottom, rgba(228,244,251,0) 0%, var(--water-light) 45%, #d2ecf8 100%);
  }
  .water-splash {
    position: absolute; left: 0; right: 0; bottom: 0; height: 115px;
    background: linear-gradient(to bottom, rgba(143,208,239,0.2) 0%, var(--water-mid) 45%, var(--water-deep) 70%, #bfe3f5 100%);
  }
  .memberships { position: absolute; left: 41px; top: 45px; display: flex; align-items: center; }
  .badge-square { width: 30px; height: 34px; border-radius: 6px; background: var(--badge); }
  .badge-divider { width: 1px; height: 34px; background: var(--badge); margin: 0 18px 0 19px; }
  .badge-wide { width: 118px; height: 30px; background: var(--badge); border-radius: 2px; }
  .services { position: absolute; left: 39px; top: 94px; list-style: none; }
  .services li {
    position: relative; padding-left: 13px; height: 19px;
    font-family: "Roboto Condensed", "Arial Narrow", sans-serif; font-size: 14.5px; color: var(--ink);
  }
  .services li::before {
    content: ""; position: absolute; left: 1px; top: 7px;
    width: 6px; height: 6px; border-radius: 50%; background: var(--navy);
  }
  .brand { position: absolute; left: 380px; top: 62px; display: flex; align-items: center; gap: 10px; }
  .brand-dot { width: 22px; height: 22px; border-radius: 50%; background: var(--coral); flex: none; }
  .brand-name {
    font-family: "Short Stack", "Comic Sans MS", cursive;
    font-size: 26px; line-height: 1.1; color: var(--navy);
  }
</style>
</head>
<body>

<section class="card card-front" aria-label="Business card front">
  <svg class="front-sweep" viewBox="0 0 600 344" aria-hidden="true">
    <path d="M0 0 H118 Q215 172 150 344 H0 Z" fill="var(--coral)"/>
    <path d="M118 -4 Q215 172 150 348" fill="none" stroke="var(--white)" stroke-width="20"/>
  </svg>
  <div class="front-brand">
    <span class="front-brand-dot"></span>
    <span class="front-brand-name">Crestline<br>Bathrooms</span>
  </div>
  <h1 class="holder-name">Daniel Hartwell</h1>
  <ul class="contact-list">
    <li>0412 555 018
      <svg viewBox="0 0 24 24" aria-hidden="true"><path d="M6.6 10.8a15.1 15.1 0 0 0 6.6 6.6l2.2-2.2a1 1 0 0 1 1-.25 11.4 11.4 0 0 0 3.6.57 1 1 0 0 1 1 1V20a1 1 0 0 1-1 1A17 17 0 0 1 3 4a1 1 0 0 1 1-1h3.5a1 1 0 0 1 1 1c0 1.25.2 2.45.57 3.57a1 1 0 0 1-.25 1z"/></svg>
    </li>
    <li>6100 4729
      <svg viewBox="0 0 24 24" aria-hidden="true"><path d="M7 1h10a2 2 0 0 1 2 2v18a2 2 0 0 1-2 2H7a2 2 0 0 1-2-2V3a2 2 0 0 1 2-2zm0 3v14h10V4zm5 15.2a1.2 1.2 0 1 0 0 2.4 1.2 1.2 0 0 0 0-2.4z"/></svg>
    </li>
    <li>daniel@crestlinebathrooms.com.au
      <svg viewBox="0 0 24 24" aria-hidden="true"><path d="M2 5h20v14H2zm2 2v.5l8 5 8-5V7l-8 5z"/></svg>
    </li>
    <li>crestlinebathrooms.com.au
      <svg viewBox="0 0 24 24" aria-hidden="true"><path d="M12 2a10 10 0 1 0 0 20 10 10 0 0 0 0-20zm-1 17.9A8 8 0 0 1 4.1 10H7l2 2v2l2 2zm6.9-2.5A2 2 0 0 0 16 16h-1v-3a1 1 0 0 0-1-1H8v-2h2a1 1 0 0 0 1-1V7h2a2 2 0 0 0 2-2v-.4a8 8 0 0 1 2.9 12.8z"/></svg>
    </li>
    <li class="postal">PO Box 41, Larkfield 2620</li>
  </ul>
</section>

<section class="card card-back" aria-label="Business card back">
  <div class="water-glow"></div>
  <div class="water-splash" role="img" aria-label="Flowing water wave with splashing droplets"></div>
  <div class="memberships" aria-label="Industry memberships">
    <div class="badge-square"></div>
    <div class="badge-divider"></div>
    <div class="badge-wide"></div>
  </div>
  <ul class="services">
    <li>Complete Bathroom Renovations &amp; Remodelling</li>
    <li>Highly Skilled &amp; Qualified Tradespeople</li>
    <li>Professional Service From Concept To Completion</li>
    <li>All Work Guaranteed</li>
  </ul>
  <div class="brand">
    <span class="brand-dot"></span>
    <span class="brand-name">Crestline<br>Bathrooms</span>
  </div>
</section>

</body>
</html>
```